Charity Initiative needs a WebPage design

We need a web design for charity initiative by two young guys riding their bikes around Australia to support HarbourLight which helps people with depression and anxiety. Full brief and requirements are attached in the PDF and word document. We have the logo already done and attached. Website will be done in Wordpress and need to get Donations, display current donations, show live Video feed, GPS tracker, Blogs etc and also ability to sell merchandise later

Target Market(s)

Sponsors, Business, Young People

Number of Pages Required

4 page

Font styles to use
Serif
Sans Serif
Decorative
Script

Requirements
Must have
• As per Brief and also Donation status etc
Nice to have
• Please check my logo and read the Bried

```html
<!DOCTYPE html>
<html lang="en">
<head>
<meta charset="utf-8">
<title>Ride the Horizon</title>
<link href="https://fonts.googleapis.com/css2?family=Oswald:wght@400;500&family=Roboto:wght@400;500;700&display=swap" rel="stylesheet">
<style>
:root{
  --pink:#e6185a;
  --pink-dark:#c4124b;
  --teal:#43b9b0;
  --teal-dark:#2b8f89;
  --ink:#333;
  --muted:#777;
  --dark:#101314;
  --darker:#070909;
  --white:#fff;
}
*{box-sizing:border-box;margin:0;padding:0}
html,body{width:1200px;height:2258px;overflow:hidden}
body{position:relative;background:var(--white);font-family:'Roboto',sans-serif;color:var(--ink)}
.abs{position:absolute}
.display{font-family:'Oswald',sans-serif;font-weight:400;text-transform:uppercase}

/* header */
.site-header{left:0;top:0;width:1200px;height:128px;background:var(--white)}
.brand{left:113px;top:44px;display:flex;align-items:center;gap:10px;font-family:'Oswald',sans-serif;font-weight:500;font-size:30px;color:var(--pink)}
.brand-dot{width:24px;height:24px;border-radius:50%;background:var(--pink)}
.social{top:18px;width:30px;height:30px;border-radius:50%;background:#e4e6e6}
.nav-band{left:0;top:0}
.nav-item{top:80px;height:36px;line-height:36px;font-size:11px;font-weight:500;color:var(--white);text-transform:uppercase;text-align:center}
.nav-item.is-active{background:var(--teal-dark);width:65px;left:396px;box-shadow:inset 0 0 0 1px rgba(0,0,0,.08)}
.donate-btn{left:910px;top:75px;width:177px;height:42px;line-height:42px;background:var(--pink);color:var(--white);font-size:11px;font-weight:500;text-align:center;text-transform:uppercase}

/* hero */
.hero{left:0;top:128px;width:1200px;height:504px;background:linear-gradient(100deg,#4d5563 0%,#9c7a5a 35%,#c9a070 55%,#6b5448 78%,#2a2522 100%)}
.hero-title{left:111px;top:305px;font-size:45px;color:var(--white);letter-spacing:.5px}
.hero-text{left:111px;top:376px;width:640px;font-size:14px;line-height:22px;color:var(--white)}
.hero-btn{left:111px;top:452px;width:264px;height:63px;background:linear-gradient(#e3386f,var(--pink-dark));color:var(--white);display:flex;align-items:center;justify-content:center;gap:10px;font-family:'Oswald',sans-serif;font-size:17px;text-transform:uppercase}
.dot{top:595px;width:13px;height:13px;border-radius:50%;background:#d6d6d6}
.dot.is-active{background:transparent;border:2px solid var(--pink)}

/* welcome */
.welcome-title{left:0;top:682px;width:1200px;text-align:center;font-size:30px;color:var(--ink)}
.welcome-title span,.accent-pink{color:var(--pink)}
.welcome-text{left:117px;top:730px;width:966px;text-align:center;font-size:11.5px;line-height:32px;color:var(--muted)}

/* donations */
.donations{left:0;top:851px;width:1200px;height:230px;background:var(--pink)}
.donations-title{left:0;top:894px;width:1200px;text-align:center;font-size:29px;color:var(--white)}
.progress-track{left:251px;top:985px;width:668px;height:12px;border-radius:6px;background:#1e1e24}
.progress-fill{left:251px;top:985px;width:400px;height:12px;border-radius:6px;background:linear-gradient(#5fd0c6,var(--teal-dark))}
.progress-tag{left:652px;top:960px;width:36px;height:18px;border-radius:3px;background:#3a6d6a;color:var(--white);font-size:9px;line-height:18px;text-align:center}
.stat{color:var(--white);text-align:center}
.stat-value{font-size:19px}
.stat-label{font-size:11px}

/* videos */
.videos{left:0;top:1081px;width:1200px;height:497px;background:radial-gradient(circle at 85% 30%,#3b3e40 0%,#1b1d1e 45%,#0c0d0d 100%)}
.videos-title{left:0;top:1130px;width:1200px;text-align:center;font-size:29px;color:var(--white)}
.videos-title span{color:var(--teal)}
.video-card{top:1214px;width:450px;height:312px;background:var(--white)}
.video-card h3{position:absolute;left:0;top:34px;width:100%;text-align:center;font-size:14px;font-weight:400;text-transform:uppercase;color:var(--ink)}
.video-frame{position:absolute;left:29px;top:77px;width:392px;height:195px;display:flex;align-items:center;justify-content:center}
.video-frame.mountain{background:linear-gradient(#9aa59a,#4f6a3c 55%,#3a4d2c)}
.video-frame.coast{background:linear-gradient(#8fb3d8,#3f7fb2 55%,#b79a7a 80%)}

/* tracker + journal */
.map{left:0;top:1578px;width:516px;height:386px;background:linear-gradient(135deg,#a9c9f2,#d7dcb9 45%,#cfd9b0 70%,#a9c9f2)}
.track-strip{left:516px;top:1578px;width:70px;height:386px;background:var(--pink)}
.track-label{left:516px;top:1578px;width:70px;height:386px;display:flex;align-items:center;justify-content:center}
.track-label span{transform:rotate(-90deg);white-space:nowrap;font-size:27px;color:var(--white)}
.journal-title{left:610px;top:1606px;font-size:29px;color:var(--ink)}
.journal-thumb{left:613px;width:149px;height:103px;box-shadow:0 2px 4px rgba(0,0,0,.25);overflow:hidden}
.journal-thumb .date{position:absolute;left:0;bottom:0;width:100%;height:33px;line-height:33px;background:var(--teal);color:var(--white);font-size:11px;text-align:center}
.journal-thumb.night{background:linear-gradient(#1c1a18,#7a4a18 60%,#d0902a)}
.journal-thumb.road{background:linear-gradient(#9ec3c8,#5b6f6a 60%,#2f3a38)}
.journal-head{left:788px;width:300px;font-size:11.5px;font-weight:500;line-height:26px;color:var(--ink)}
.journal-body{left:788px;width:300px;font-size:11px;line-height:26px;color:var(--muted)}

/* footer */
.footer{left:0;top:1964px;width:1200px;height:215px;background:var(--dark)}
.footer-bottom{left:0;top:2179px;width:1200px;height:79px;background:var(--darker)}
.footer-heading{top:1996px;font-size:16px;color:var(--white)}
.footer-text{font-size:11px;line-height:23px;color:var(--white)}
.footer-brand{left:113px;top:2052px;display:flex;align-items:center;gap:8px;font-family:'Oswald',sans-serif;font-size:16px;color:var(--white)}
.footer-brand i{width:14px;height:14px;border-radius:50%;background:var(--teal);display:block}
.footer-links{left:450px;top:2034px;list-style:none}
.footer-links li{font-size:11px;line-height:24px;color:var(--white)}
.footer-links li::before{content:"";display:inline-block;border-left:5px solid var(--white);border-top:4px solid transparent;border-bottom:4px solid transparent;margin-right:7px}
.news-input{left:885px;top:2089px;width:145px;height:29px;background:#eee;font-size:11px;line-height:29px;padding-left:12px;color:#333}
.news-btn{left:1030px;top:2089px;width:54px;height:29px;background:var(--pink);color:var(--white);font-size:10px;line-height:29px;text-align:center;text-transform:uppercase}
.copyright{left:0;top:2212px;width:1200px;text-align:center;font-size:11px;color:var(--white)}
</style>
</head>
<body>

<header class="site-header abs">
  <div class="brand abs"><span class="brand-dot"></span>Ride the Horizon</div>
  <span class="social abs" style="left:986px"></span>
  <span class="social abs" style="left:1022px"></span>
  <span class="social abs" style="left:1058px"></span>
  <svg class="nav-band abs" width="1200" height="130" aria-hidden="true">
    <polygon points="384,68 1200,68 1200,125 354,125" fill="#43b9b0"/>
    <line x1="0" y1="126" x2="1200" y2="126" stroke="#43b9b0" stroke-width="3"/>
  </svg>
  <nav>
    <div class="nav-item is-active abs">Home</div>
    <div class="nav-item abs" style="left:491px;width:60px">Journal</div>
    <div class="nav-item abs" style="left:589px;width:60px">Riders</div>
    <div class="nav-item abs" style="left:684px;width:90px">Supporters</div>
    <div class="nav-item abs" style="left:808px;width:70px">Contact</div>
  </nav>
  <div class="donate-btn abs">Make a Donation</div>
</header>

<section>
  <div class="hero abs" role="img" aria-label="Photo of a motorcyclist riding down an open highway at sunset"></div>
  <h1 class="hero-title display abs">Two mates. Two bikes. One long road.</h1>
  <p class="hero-text abs">Lorem ipsum dolor sit amet, consectetur adipiscing elit. Nulla rhoncus semper eros, vitae semper magna mollis vel.</p>
  <div class="hero-btn abs">
    <svg width="14" height="14" viewBox="0 0 14 14" aria-hidden="true"><circle cx="7" cy="7" r="7" fill="#fff"/><path d="M5 4l4 3-4 3z" fill="#c4124b"/></svg>
    Get Donations
  </div>
  <span class="dot abs" style="left:559px"></span>
  <span class="dot abs" style="left:582px"></span>
  <span class="dot is-active abs" style="left:605px"></span>
  <span class="dot abs" style="left:628px"></span>
</section>

<section>
  <h2 class="welcome-title display abs">Welcome to <span>Ride the Horizon</span></h2>
  <p class="welcome-text abs">Aliquam sit amet sagittis justo. Nunc vitae velit sed mauris pulvinar eleifend pulvinar vel justo. Etiam nulla odio, lacinia non blandit at, aliquam vitae sapien. Donec sit amet cursus leo. Morbi imperdiet, mauris et efficitur placerat, odio arcu faucibus erat, sit amet placerat ligula erat vel tortor. Nulla consectetur dictum mi id bibendum. Cras viverra vitae diam ut sodales. Suspendisse bibendum ac nunc quis ornare. Nunc libero lacus, egestas nec molestie ac, molestie quis lorem.</p>
</section>

<section>
  <div class="donations abs"></div>
  <h2 class="donations-title display abs">Current Donations</h2>
  <div class="progress-track abs"></div>
  <div class="progress-fill abs"></div>
  <div class="progress-tag abs">60%</div>
  <div class="stat abs" style="left:167px;top:974px;text-align:left"><div class="stat-value">$ 1,172</div><div class="stat-label">Raised</div></div>
  <div class="stat abs" style="left:938px;top:974px;text-align:left"><div class="stat-value">$ 2,000</div><div class="stat-label">Goal</div></div>
  <div class="stat abs" style="left:550px;top:1015px;width:100px"><div class="stat-value">367</div><div class="stat-label">Donors</div></div>
</section>

<section>
  <div class="videos abs" role="img" aria-label="Dark close-up of a motorcycle headlight as section background"></div>
  <h2 class="videos-title display abs">Our <span>Live Videos</span></h2>
  <article class="video-card abs" style="left:120px">
    <h3>Nulla rhoncus semper eros, vitae semper magna</h3>
    <div class="video-frame mountain" role="img" aria-label="Video still of a rider on a mountain valley road">
      <svg width="54" height="54" aria-hidden="true"><circle cx="27" cy="27" r="24" fill="rgba(255,255,255,.25)" stroke="#fff" stroke-width="3"/><path d="M22 17l13 10-13 10z" fill="#fff"/></svg>
    </div>
  </article>
  <article class="video-card abs" style="left:628px">
    <h3>Integer nec turpis fermentum turpis varius</h3>
    <div class="video-frame coast" role="img" aria-label="Video still of a motorcycle parked by the sea">
      <svg width="54" height="54" aria-hidden="true"><circle cx="27" cy="27" r="24" fill="rgba(255,255,255,.25)" stroke="#fff" stroke-width="3"/><path d="M22 17l13 10-13 10z" fill="#fff"/></svg>
    </div>
  </article>
</section>

<section>
  <div class="map abs" role="img" aria-label="Live map of Australia showing the riders' current location"></div>
  <div class="track-strip abs"></div>
  <div class="track-label abs"><span class="display">Track our bikes</span></div>
  <h2 class="journal-title display abs">Recent <span class="accent-pink">Journal</span></h2>

  <div class="journal-thumb night abs" style="top:1675px" role="img" aria-label="Night road with motorcycle light trails"><div class="date">Mar 02, 2016</div></div>
  <p class="journal-head abs" style="top:1668px">Lorem ipsum dolor sit amet, consectetur adipiscing elit. Integer enim mauris, iaculis sit amet</p>
  <p class="journal-body abs" style="top:1728px">Duis dapibus nisi eget ultricies posuere. Sed non elit id risus commodo fermentum.</p>

  <div class="journal-thumb road abs" style="top:1825px" role="img" aria-label="Two riders on the road"><div class="date">Mar 02, 2016</div></div>
  <p class="journal-head abs" style="top:1820px">Duis dapibus nisi eget ultricies posuere. Sed non elit id risus commodo fermentum.</p>
  <p class="journal-body abs" style="top:1880px">Suspendisse viverra laoreet elit, non lacinia eros imperd iet a. Nunc aliquam blandit ipsum, a placerat eros.</p>
</section>

<footer>
  <div class="footer abs"></div>
  <h3 class="footer-heading display abs" style="left:111px">HarbourLight</h3>
  <div class="footer-brand abs"><i></i>HarbourLight</div>
  <p class="footer-text abs" style="left:113px;top:2101px;width:300px">Aenean commodo lorem dui, quis laoreet dolor blandit ac. Lorem ipsum dolor sit amet, consectetur.</p>

  <h3 class="footer-heading display abs" style="left:450px">Links</h3>
  <ul class="footer-links abs">
    <li>Journal</li><li>Riders</li><li>Supporters</li><li>FAQs</li><li>Contact Us</li>
  </ul>

  <h3 class="footer-heading display abs" style="left:636px">Get in touch</h3>
  <p class="footer-text abs" style="left:636px;top:2035px;width:230px;line-height:25px">Address : 218 Coastline Road, Suite<br>Lorem Ipsm - 123 456</p>
  <p class="footer-text abs" style="left:636px;top:2092px">Phone : (305) 555-0148</p>
  <p class="footer-text abs" style="left:636px;top:2128px">Email : info@ridehorizon.org</p>

  <h3 class="footer-heading display abs" style="left:885px">Newsletter</h3>
  <p class="footer-text abs" style="left:885px;top:2032px;width:200px;line-height:18px">Your about us information would fit here nicely.</p>
  <div class="news-input abs">Email address</div>
  <div class="news-btn abs">Submit</div>

  <div class="footer-bottom abs"></div>
  <p class="copyright abs">Copyright © 2016. All Rights Reserved</p>
</footer>

</body>
</html>
```